Construction company business card

One side to be the logo with the company name, The other side I would like: (Tomas verbick) Project manager 41 barrow crescent hallam 52917306224783(03) 9703 2428Info@gudeljgroup.comAnd then maybe a couple dot points saying what we do:Construction (commercial & industrial) Civil construction

Anything else please contact me!
Maybe curved st one edge of the card

Target Market(s)

Older clientele

Industry/Entity Type

Construction Company

Contact Information for Business Card

Read above

Colors
3277b5
1b1b1b
9d9d9d

Requirements
Must have
• Use my logo on one side
Nice to have
• Read above
Should not have
• Read above

```html
<!DOCTYPE html>
<html lang="en">
<head>
<meta charset="utf-8">
<title>Stonebay Contractors – Business Card</title>
<link href="https://fonts.googleapis.com/css2?family=Open+Sans:wght@400;600;700&display=swap" rel="stylesheet">
<style>
  :root {
    --brand-blue: #3277b5;
    --brand-black: #1b1b1b;
    --brand-grey: #9d9d9d;
    --paper: #ffffff;
    --backdrop: #d4d4d4;
    --text-grey: #555555;
  }
  * { box-sizing: border-box; margin: 0; padding: 0; }
  html, body {
    width: 1200px; height: 900px; overflow: hidden;
    background: var(--backdrop);
    font-family: "Open Sans", sans-serif;
  }
  .stage { position: relative; width: 1200px; height: 900px; }

  /* Front side: dark, rounded top */
  .card-front {
    position: absolute; left: 130px; top: 170px;
    width: 320px; height: 560px;
    background: var(--brand-black);
    border-radius: 160px 160px 0 0;
    box-shadow: 0 6px 18px rgba(0,0,0,.25);
  }
  .front-brand {
    position: absolute; top: 70px; left: 0; right: 0;
    display: flex; flex-direction: column; align-items: center; gap: 20px;
  }
  .brand-dot {
    width: 150px; height: 150px; border-radius: 50%;
    border: 22px solid var(--brand-blue);
  }
  .front-brand .brand-name {
    color: var(--brand-blue); font-weight: 700; font-size: 24px; letter-spacing: 2px;
    text-align: center; line-height: 1.2; text-transform: uppercase;
  }
  .services {
    position: absolute; left: 0; right: 0; bottom: 70px;
    text-align: center; font-weight: 600; font-size: 14px; line-height: 1.6;
    color: var(--paper); letter-spacing: .5px;
  }
  .services .sector { color: var(--brand-blue); font-weight: 600; }

  /* Back side: white, rounded left end */
  .card-back {
    position: absolute; left: 520px; top: 300px;
    width: 560px; height: 320px;
    background: var(--paper);
    border-radius: 160px 0 0 160px;
    box-shadow: 0 6px 18px rgba(0,0,0,.2);
  }
  .back-brand {
    position: absolute; left: 38px; top: 0; bottom: 0; width: 220px;
    display: flex; align-items: center; gap: 12px;
  }
  .back-brand .brand-mark {
    flex: none; width: 46px; height: 46px; border-radius: 50%;
    border: 8px solid var(--brand-blue);
  }
  .back-brand .brand-name {
    color: var(--brand-blue); font-weight: 700; font-size: 17px; line-height: 1.2;
    letter-spacing: 1px; text-transform: uppercase;
  }
  .divider {
    position: absolute; left: 270px; top: 70px; width: 1px; height: 190px;
    background: var(--brand-grey);
  }
  .contact { position: absolute; left: 292px; top: 44px; color: var(--text-grey); }
  .contact .person-name { color: var(--brand-blue); font-weight: 700; font-size: 19px; text-transform: uppercase; }
  .contact .person-role { font-size: 13px; margin-bottom: 22px; }
  .contact .address { font-size: 13px; line-height: 1.45; margin-bottom: 10px; }
  .contact ul { list-style: none; font-size: 13px; line-height: 1.75; }
  .contact li { display: flex; align-items: center; gap: 7px; }
  .contact svg { width: 12px; height: 12px; fill: none; stroke: var(--brand-blue); stroke-width: 2; flex: none; }
</style>
</head>
<body>
<main class="stage">
  <section class="card-front">
    <div class="front-brand">
      <div class="brand-dot"></div>
      <p class="brand-name">Stonebay Contractors</p>
    </div>
    <div class="services">
      <p>CONSTRUCTION</p>
      <p class="sector">(COMMERCIAL &amp; INDUSTRIAL)</p>
      <p>CIVIL CONSTRUCTION</p>
    </div>
  </section>

  <section class="card-back">
    <div class="back-brand">
      <div class="brand-mark"></div>
      <p class="brand-name">Stonebay<br>Contractors</p>
    </div>
    <div class="divider"></div>
    <div class="contact">
      <p class="person-name">Tomas Verbick</p>
      <p class="person-role">Project Manager</p>
      <p class="address">41 Barrow Crescent<br>Kelsworth 5291</p>
      <ul>
        <li><svg viewBox="0 0 12 12"><path d="M2 1.5l2 0 1 2.5-1.3 1a6 6 0 0 0 3.3 3.3l1-1.3 2.5 1v2a1 1 0 0 1-1 1A9 9 0 0 1 1 2.5a1 1 0 0 1 1-1z"/></svg>(03) 9418 6573</li>
        <li><svg viewBox="0 0 12 12"><rect x="3" y="1" width="6" height="10" rx="1"/></svg>730 622 4783</li>
        <li><svg viewBox="0 0 12 12"><rect x="1" y="2.5" width="10" height="7"/><path d="M1 2.5l5 4 5-4"/></svg>Info@verbickgroup.com</li>
        <li><svg viewBox="0 0 12 12"><circle cx="6" cy="6" r="5"/><path d="M1 6h10M6 1c2.5 3 2.5 7 0 10M6 1c-2.5 3-2.5 7 0 10"/></svg>www.verbickgroup.com</li>
      </ul>
    </div>
  </section>
</main>
</body>
</html>
```